Business Card Design

We are a commercial real estate brokerage in San Francisco, leasing office buildings downtown.
I would like a clean, elegant look. Simple but powerful .

Industry/Entity Type

Business

Contact Information for Business Card

Derek Holloway
lic# 07258143
415.555.0172
derek@velt-commercial.example
velt-commercial.example

```html
<!DOCTYPE html>
<html lang="en">
<head>
<meta charset="utf-8">
<title>Velt Commercial – Business Card</title>
<link rel="stylesheet" href="https://fonts.googleapis.com/css2?family=Open+Sans:wght@400;600&display=swap">
<style>
  :root {
    --backdrop: #e9e4da;
    --card: #ffffff;
    --slate: #7886a3;
    --slate-light: #c9d0dc;
    --bar-text: #ffffff;
  }
  * { margin: 0; padding: 0; box-sizing: border-box; }
  html, body {
    width: 1200px;
    height: 510px;
    overflow: hidden;
    background: var(--backdrop);
  }
  .card {
    position: absolute;
    left: 182px;
    top: 10px;
    width: 836px;
    height: 490px;
    background: var(--card);
    border-radius: 22px;
    overflow: hidden;
    font-family: "Open Sans", Arial, sans-serif;
  }
  .brand {
    position: absolute;
    left: 68px;
    top: 196px;
    display: flex;
    align-items: center;
    gap: 22px;
    color: var(--slate);
    font-weight: 600;
  }
  .brand-square {
    width: 92px;
    height: 92px;
    background: var(--slate);
  }
  .brand-name {
    display: flex;
    flex-direction: column;
    line-height: 1;
  }
  .brand-name .primary {
    font-size: 64px;
    letter-spacing: 1px;
  }
  .brand-name .secondary {
    font-size: 27px;
    letter-spacing: 0.5px;
    margin-top: 6px;
  }
  .contact {
    position: absolute;
    left: 524px;
    top: 0;
    width: 312px;
    list-style: none;
  }
  .contact-bar {
    position: absolute;
    left: 0;
    width: 312px;
    height: 28px;
    background: var(--slate);
    color: var(--bar-text);
    font-size: 17px;
    line-height: 28px;
    padding-left: 12px;
    white-space: nowrap;
  }
  .contact-bar.name { top: 122px; font-size: 19px; }
  .accent-band {
    position: absolute;
    left: 0;
    top: 162px;
    width: 312px;
    height: 32px;
    background: var(--slate-light);
  }
  .contact-bar.license { top: 210px; }
  .contact-bar.phone { top: 252px; }
  .contact-bar.email { top: 294px; }
  .contact-bar.web { top: 338px; }
</style>
</head>
<body>
  <main class="card">
    <div class="brand">
      <div class="brand-square"></div>
      <div class="brand-name">
        <span class="primary">VELT</span>
        <span class="secondary">COMMERCIAL</span>
      </div>
    </div>
    <ul class="contact">
      <li class="contact-bar name">Derek Holloway</li>
      <li class="accent-band" role="img" aria-label="Decorative diagonal hatched band"></li>
      <li class="contact-bar license">lic# 07258143</li>
      <li class="contact-bar phone">415.555.0172</li>
      <li class="contact-bar email">derek@velt-commercial.example</li>
      <li class="contact-bar web">velt-commercial.example</li>
    </ul>
  </main>
</body>
</html>
```